Satchel & Sundial needs new business card design

I need a new business card design. I'm looking for out-of-the-box design which represents the freedom of being a location independent entrepreneur.
I offer coaching, retreats and trips.
I would like to see designs with and without the photo.
Colors I use are black (#000000), green (#25A796) and brown (#D7C38C)
Website satchelandsundial.example

Target Market(s)

location independent entrepreneurs, digital nomads, people looking to swap the 9 to 5 for a lifestyle business

Industry/Entity Type

Business

Contact Information for Business Card

Dorota Falkner
Your Lifestyle Business Coach, Retreat & Trip Leader
http://satchelandsundial.example
hello@satchelandsundial.example
Live a life you don't need a holiday from

Font styles to use
Serif
Sans Serif

Requirements
Must have
• One side should contain only the logo. I would also consider having the "Live a life you don't need a holiday from" on that side too (depending on how it looks)
• Please show both sides on the designs.

```html
<!DOCTYPE html>
<html lang="en">
<head>
<meta charset="utf-8">
<title>Satchel &amp; Sundial – Business Card</title>
<link rel="stylesheet" href="https://fonts.googleapis.com/css2?family=Source+Sans+3:wght@400;600;700&display=swap">
<style>
  :root {
    --stage: #000000;
    --sand: #D6C28C;
    --teal: #25A796;
    --ink: #1e1e1e;
    --rule: #3a3428;
    --logo-light: #E4D3A2;
  }
  * { box-sizing: border-box; margin: 0; padding: 0; }
  html, body {
    width: 1200px;
    height: 900px;
    overflow: hidden;
    background: var(--stage);
    font-family: "Source Sans 3", "Myriad Pro", Arial, sans-serif;
  }
  .canvas { position: relative; width: 1200px; height: 900px; }

  .card { position: absolute; top: 275px; width: 477px; height: 293px; }

  .card--front {
    left: 116px;
    background: var(--sand);
    border-radius: 0 52px 0 52px;
    color: var(--ink);
  }
  .card--back {
    left: 622px;
    top: 276px;
    height: 292px;
    background: var(--teal);
    border-radius: 52px 0 52px 0;
  }

  .wordmark {
    position: absolute;
    font-weight: 600;
    letter-spacing: 1px;
    text-transform: uppercase;
    white-space: nowrap;
  }
  .card--front .wordmark {
    right: 30px;
    top: 46px;
    font-size: 31px;
    color: var(--ink);
  }
  .card--back .wordmark {
    left: 0; right: 0;
    top: 118px;
    text-align: center;
    font-size: 38px;
    color: var(--logo-light);
  }

  .holder { position: absolute; left: 33px; top: 142px; }
  .holder__name { font-size: 16px; font-weight: 700; line-height: 1.2; }
  .holder__role { font-size: 13px; font-weight: 400; margin-top: 4px; }

  .divider {
    position: absolute;
    left: 0; right: 0; top: 196px;
    height: 1.5px;
    background: var(--rule);
  }

  .contact {
    position: absolute;
    right: 28px;
    top: 205px;
    list-style: none;
    text-align: right;
    font-size: 13px;
    line-height: 17px;
  }
  .contact__item { display: flex; justify-content: flex-end; align-items: center; gap: 6px; }
  .contact__icon { width: 9px; height: 9px; fill: var(--ink); }

  .motto {
    position: absolute;
    right: 30px;
    top: 249px;
    font-size: 13px;
    font-weight: 700;
    text-transform: uppercase;
    letter-spacing: 0.1px;
  }
</style>
</head>
<body>
<main class="canvas">

  <section class="card card--front" aria-label="Card front">
    <div class="wordmark">Satchel &amp; Sundial</div>

    <div class="holder">
      <p class="holder__name">Dorota Falkner</p>
      <p class="holder__role">Your Lifestyle Business Coach Retreat &amp; Trip Leader</p>
    </div>

    <div class="divider"></div>

    <ul class="contact">
      <li class="contact__item">
        <span>hello@satchelandsundial.example</span>
        <svg class="contact__icon" viewBox="0 0 10 10" aria-hidden="true">
          <rect x="0" y="1.5" width="10" height="7" rx="0.6"/>
          <path d="M0.6 2.2 L5 5.6 L9.4 2.2" fill="none" stroke="#D6C28C" stroke-width="1"/>
        </svg>
      </li>
      <li class="contact__item">
        <span>www.satchelandsundial.example</span>
        <svg class="contact__icon" viewBox="0 0 10 10" aria-hidden="true">
          <circle cx="5" cy="5" r="5"/>
          <path d="M2.5 3 Q4 2 5 3.5 T7.5 4 M3 6.5 Q5 6 6 8" fill="none" stroke="#D6C28C" stroke-width="0.9"/>
        </svg>
      </li>
    </ul>

    <p class="motto">Live a life you don't need a holiday from</p>
  </section>

  <section class="card card--back" aria-label="Card back">
    <div class="wordmark">Satchel &amp; Sundial</div>
  </section>

</main>
</body>
</html>
```